Email signatures and letterhead for in-house lawyers and staff

I need Word, Outlook, and Gmail compatible letterhead and email signature block for an in-house litigation group. Simple and generic is the goal! The design must be user-modifiable for several locations and job titles. The design will work best if created in MS Word. We are an in-house group of trial lawyers, about 40 persons total, operating from nine locations, and providing services in ten US states. Letterhead will be used in header of MSWord documents. Email sig will be used in both Outlook and Gmail. The office name will be different in each of our locations, so the design has to be user-modifiable.

Industry/Entity Type

Law Firm

Font styles to use
Sans Serif

Requirements
Must have
• A fresher, more professional look than the screenshots I've posted

The screenshot with multiple attorney names in the office is most representative of the info we want included.
Nice to have
• Sylish but not overly so. Generic legal symbols might be appropriate, but can't look like tired old clip art.
Should not have
• watermarks

```html
<!DOCTYPE html>
<html lang="en">
<head>
<meta charset="utf-8">
<title>Letterhead and Email Signature – Law Office of Daniel R. Carter</title>
<link rel="stylesheet" href="https://fonts.googleapis.com/css2?family=Fira+Sans+Condensed:wght@400;500;600&family=Roboto+Condensed:wght@400;500;700&family=Roboto:wght@300;400&display=swap">
<style>
  :root {
    --canvas: #ffffff;
    --paper: #ffffff;
    --ink: #1b1b1b;
    --ink-soft: #333333;
    --panel: #cccccc;
    --band-dark: #7a7a7a;
    --band-edge: #a9a9a9;
    --sig-blue: #2f5fb8;
    --title-gold: #a8793a;
    --rule: #cfcfcf;
    --shadow: rgba(0, 0, 0, 0.45);
  }
  * { box-sizing: border-box; margin: 0; padding: 0; }
  html, body { width: 1200px; height: 1200px; overflow: hidden; background: var(--canvas); }
  body { position: relative; font-family: "Fira Sans Condensed", "Roboto Condensed", sans-serif; color: var(--ink); }

  /* ---------- Letterhead ---------- */
  .letterhead {
    position: absolute; left: 274px; top: 84px; width: 598px; height: 776px;
    background: var(--paper);
    box-shadow: 4px 6px 14px var(--shadow);
  }
  .letterhead__band {
    position: absolute; left: 460px; top: 0; width: 16px; height: 100%;
    background: linear-gradient(90deg, var(--band-edge) 0 3px, var(--band-dark) 3px 7px, var(--band-edge) 7px 9px, var(--band-dark) 9px 16px);
  }
  .letterhead__panel {
    position: absolute; left: 476px; top: 0; width: 122px; height: 100%;
    background: var(--panel);
  }
  .firm-mark {
    position: absolute; left: 41px; top: 30px; width: 40px; height: 40px;
    background: var(--ink);
  }
  .firm-name {
    position: absolute; left: 0; top: 100px; width: 100%;
    text-align: center; font-family: "Roboto Condensed", sans-serif;
    font-size: 12px; line-height: 16px; letter-spacing: 0.06em; color: var(--ink);
  }
  .firm-name strong { font-weight: 700; display: block; }
  .firm-contact {
    position: absolute; right: 14px; top: 632px; text-align: right;
    font-family: "Fira Sans Condensed", sans-serif; font-weight: 600; color: var(--ink);
  }
  .firm-contact dt { font-size: 6px; line-height: 8px; }
  .firm-contact dd { font-size: 8.5px; line-height: 11px; margin-bottom: 8px; }
  .firm-contact dd.address { font-size: 9.5px; line-height: 14.5px; margin-bottom: 0; }

  .letter {
    position: absolute; left: 40px; top: 180px; width: 382px;
    font-size: 11.6px; line-height: 22px; color: var(--ink-soft);
  }
  .letter__recipient { margin-bottom: 22px; }
  .letter__body p { text-align: justify; margin-bottom: 22px; }
  .letter__closing { margin-left: 3px; font-size: 10.5px; line-height: 16px; }
  .letter__signature {
    display: block; margin: 4px 0 0 3px; width: 187px; height: 28px;
    background: linear-gradient(90deg, #e9e9e9, #dcdcdc);
  }

  /* ---------- Email signature ---------- */
  .email-sig {
    position: absolute; left: 244px; top: 894px; width: 660px; height: 262px;
    background: var(--paper);
    box-shadow: 4px 6px 14px var(--shadow);
    overflow: hidden;
  }
  .email-sig__name {
    position: absolute; left: 28px; top: 52px; width: 242px; height: 34px;
    background: linear-gradient(90deg, #dbe4f4, #c9d6ef);
  }
  .email-sig__title {
    position: absolute; left: 34px; top: 88px;
    font-family: "Roboto", sans-serif; font-weight: 400; font-size: 16px; color: var(--title-gold);
  }
  .email-sig__contact {
    position: absolute; top: 130px; font-family: "Roboto", sans-serif; font-weight: 300;
    font-size: 11.4px; line-height: 16px; color: var(--ink);
  }
  .email-sig__contact--office { left: 28px; }
  .email-sig__contact--reach { left: 206px; }
  .email-sig__rule {
    position: absolute; left: 19px; top: 174px; width: 475px; height: 1px; background: var(--rule);
  }
  .email-sig__disclaimer {
    position: absolute; left: 19px; top: 184px; width: 475px;
    font-family: "Roboto Condensed", sans-serif; font-size: 6.4px; line-height: 13.6px; color: var(--ink);
  }
  .email-sig__disclaimer p + p { margin-top: 5px; }
</style>
</head>
<body>

  <section class="letterhead" aria-label="Letterhead">
    <div class="letterhead__band"></div>
    <aside class="letterhead__panel">
      <div class="firm-mark"></div>
      <h1 class="firm-name">LAW OFFICE OF<strong>DANIEL R. CARTER</strong></h1>
      <dl class="firm-contact">
        <dt>Phone</dt><dd>555.210.4100</dd>
        <dt>Fax</dt><dd>555.210.4199</dd>
        <dt>Email</dt><dd>daniel.carter@example-trial.com</dd>
        <dt>Address</dt>
        <dd class="address">4120 Harbor Ave<br>East - Suite 310<br>Fairview, ST 20417</dd>
      </dl>
    </aside>

    <article class="letter">
      <p class="letter__recipient">To<br>The,<br>Director</p>
      <div class="letter__body">
        <p>Lorem ipsum dolor sit amet, consectetur adipiscing elit. Sed at ante. Mauris eleifend, quam a vulptate dictum, massa quam dapibus leo, eget vulputate orci purus ut lorem. In fringilla mi in ligula. Pellen tesque aliquam quam vel dolor. Nunc adipiscing. Sed quamodio, tempus ac, aliquam molestie varius ac, tellus. Vestibulum ut nulla aliquam risus rutrum interdum. Pellentesque lorem.</p>
        <p>Curabitur sit amet erat quis risus feugiat viverra. Pellentesque augue justo,sagittis et, lacinia at, venenatis non, arcu. Nunc nec libero. In cursus dictum risus. Etiam tristique nisl a nulla. Ut a orci. Curabitur dolonunc,egestas at, accumsan at, malesuada nec, magna. Nulla facilisi. Nunc volutpat. Vestibulum ante ipsum primis in faucibus orci luctus et ultrices posuere cubilia Curae; Ut sit amet orci vel mauris blandit vehicula. Nullam quis enim. Integer dignissim viverra velit. Curabitur in odio.</p>
      </div>
      <p class="letter__closing">Thanking you,</p>
      <span class="letter__signature" role="img" aria-label="Handwritten signature of Daniel R. Carter"></span>
    </article>
  </section>

  <section class="email-sig" aria-label="Email signature">
    <div class="email-sig__name" role="img" aria-label="Script signature reading Daniel R. Carter in blue"></div>
    <p class="email-sig__title">Attorney at law</p>
    <p class="email-sig__contact email-sig__contact--office">Law Office Of Daniel R. Carter<br>T: 555.210.4100| F: 555.210.4199</p>
    <p class="email-sig__contact email-sig__contact--reach">daniel.carter@example-trial.com<br>4120 Harbor Ave. East - Suite 310, Fairview, ST 20417</p>
    <div class="email-sig__rule"></div>
    <div class="email-sig__disclaimer">
      <p>The information contained in this communication from the sender is confidential. It is intended solely for use by the recipient and others authorized to receive it. If you are not the recipient, you are hereby notified that any disclosure, copying, distribution, or taking action in relation to the contents of this information is strictly prohibited and may be unlawful.</p>
      <p>The Law Office of Laura T. Benning is an unincorporated association of individual licensed attorneys employed by Northgate Mutual Insurance Group for the purpose of representing Northgate Mutual Insurance Group, its policyholders, and insureds.</p>
    </div>
  </section>

</body>
</html>
```